We need a cover designed for our book on parenting. The focus of this book is on the parents, not on the child! We like the idea of this title having a double meaning - insight as in gaining insights into parenting, and "in sight" as in looking inward as parents and how to improve ourselves rather than looking outward to improve our children. We would love for the cover to somehow represent this double meaning. I can upload an excerpt from the book soon over the next few days.

Reason: We are still reviewing the amazing designs! Thank you so much! :)

Target Market(s)

Parents with kids of any age from babies through adult children.

Requirements
Must have
• Title is: Harborlight Parenting
• Subtitle is: Steady Homes, Calmer Hearts Ahead
• Authors names: Lena Marsh, LCSW Oscar Marsh, Ph.D.

```html
<!DOCTYPE html>
<html lang="en">
<head>
<meta charset="utf-8">
<title>Harborlight Parenting – Book Cover</title>
<link rel="stylesheet" href="https://fonts.googleapis.com/css2?family=Archivo+Black&family=Arimo:ital,wght@0,700;1,700&family=Open+Sans:wght@700&display=swap">
<style>
  :root {
    --bg: #f1f1f1;
    --sky-top: #4f95cc;
    --sky-low: #a9cde3;
    --field-gold: #b9a45c;
    --field-green: #7f8f48;
    --grass-deep: #5f7033;
    --frame-black: #141414;
    --frame-dark: #2c2c2c;
    --frame-mid: #5a5a5a;
    --frame-light: #8d8d8d;
    --ink: #151515;
    --paper: #ffffff;
  }
  * { margin: 0; padding: 0; box-sizing: border-box; }
  html, body { width: 1200px; height: 1200px; overflow: hidden; background: var(--bg); }
  .spread { position: relative; width: 1200px; height: 1200px; }
  .cover {
    position: absolute; top: 200px; width: 520px; height: 790px; overflow: hidden;
    box-shadow: 0 10px 30px rgba(0,0,0,.18);
  }
  .cover--front { left: 50px; }
  .cover--back { left: 630px; }
  .cover__photo {
    position: absolute; inset: 0;
    background: linear-gradient(180deg, var(--sky-top) 0%, var(--sky-low) 34%, var(--field-gold) 46%, var(--field-green) 70%, var(--grass-deep) 100%);
  }
  .cover__frame { position: absolute; inset: 0; }
  .title {
    position: absolute; right: 30px; top: 100px; text-align: right;
    font-family: "Archivo Black", sans-serif; color: var(--ink);
    font-size: 48px; line-height: 1; letter-spacing: -1px; text-transform: uppercase;
  }
  .subtitle {
    position: absolute; left: 160px; top: 612px; width: 330px; text-align: center;
    font-family: "Arimo", sans-serif; font-style: italic; font-weight: 700;
    font-size: 25px; line-height: 1.1; color: var(--ink); transform: rotate(-13deg);
  }
  .authors {
    position: absolute; left: 235px; top: 705px; width: 250px; text-align: center;
    font-family: "Arimo", sans-serif; font-weight: 700; font-size: 23px; line-height: 1.15;
    color: var(--paper); transform: rotate(-13deg);
  }
  .back__heading {
    position: absolute; left: 140px; top: 60px; width: 350px;
    font-family: "Arimo", sans-serif; font-weight: 700; font-size: 36px; line-height: 1.08; color: var(--ink);
  }
  .back__blurb {
    position: absolute; left: 140px; top: 215px; width: 355px;
    font-family: "Open Sans", sans-serif; font-weight: 700; font-size: 16.5px; line-height: 1.4; color: var(--ink);
  }
  .back__codebox {
    position: absolute; right: 40px; bottom: 45px; width: 200px; height: 125px; background: var(--paper);
  }
</style>
</head>
<body>
<main class="spread">
  <section class="cover cover--front">
    <div class="cover__photo" role="img" aria-label="Photo of a young mother, father and little daughter sitting together in tall summer grass under a clear blue sky"></div>
    <svg class="cover__frame" viewBox="0 0 520 790" width="520" height="790" aria-hidden="true">
      <path d="M0 0 H520 V0 L520 60 Q470 20 400 0 Z" fill="var(--frame-black)"/>
      <path d="M440 0 H520 V90 Q490 30 440 0 Z" fill="var(--frame-black)"/>
      <path d="M0 0 H210 Q90 40 40 140 Q10 220 0 300 Z" fill="var(--frame-mid)"/>
      <path d="M0 40 Q80 10 200 20 Q90 70 40 200 Q15 280 0 420 Z" fill="var(--frame-black)"/>
      <path d="M0 560 Q60 700 220 735 Q400 760 520 680 V790 H0 Z" fill="var(--frame-dark)"/>
      <path d="M40 790 Q120 700 300 690 Q430 680 520 620 V790 Z" fill="var(--frame-light)"/>
      <path d="M180 790 Q260 720 380 712 Q470 705 520 660 V790 Z" fill="var(--frame-mid)"/>
      <path d="M0 740 Q120 770 260 790" stroke="var(--paper)" stroke-width="4" fill="none"/>
      <path d="M0 755 Q110 782 220 790" stroke="var(--frame-black)" stroke-width="10" fill="none"/>
    </svg>
    <h1 class="title">Harborlight<br>Parenting</h1>
    <p class="subtitle">Steady Homes,<br>Calmer Hearts Ahead</p>
    <p class="authors">Lena Marsh, LCSW<br>&amp; Oscar Marsh, Ph.D</p>
  </section>

  <section class="cover cover--back">
    <div class="cover__photo" role="img" aria-label="Photo of a grassy hillside under blue sky with a small family walking, child on father's shoulders"></div>
    <h2 class="back__heading">Steady Homes,<br>Calmer Hearts<br>Ahead</h2>
    <p class="back__blurb">We need a cover designed for our book on parenting. The focus of this book is on the parents, not on the child! We like the idea of this title having a double meaning - insight as in gaining insights into parenting, and "in sight" as in looking inward as parents and how to improve ourselves rather than looking outward to improve our children. We would love for the cover to somehow represent this double meaning. I can upload an excerpt from the book soon over the next few days.</p>
    <div class="back__codebox"></div>
  </section>
</main>
</body>
</html>
```